Cedarvale Ridge College

We are looking to update our current webpage at www.cedarvaleridge.ca. We would like to make it modern, fresh and appealing to students. We want to keep our logo the same with the logo colours blended in as the primary colours and focus. We are open to reconfiguring content as well.
Reason: Hi, In the next 3 days we will have narrowed our search to 3 designs and will make a choice before the final deadline...
College

```html
<!DOCTYPE html>
<html lang="en">
<head>
<meta charset="utf-8">
<title>Cedarvale Ridge College</title>
<link rel="stylesheet" href="https://fonts.googleapis.com/css2?family=Lato:wght@400;700&family=Oswald:wght@400&family=Bree+Serif&family=Open+Sans:wght@300;400;700&display=swap">
<style>
:root{
  --green-dark:#003f35;
  --green-line:#00382f;
  --teal:#336e64;
  --navy:#0d2356;
  --header-bg:#efefef;
  --text:#333333;
  --muted:#555555;
  --white:#ffffff;
  --rule:#b9b9b9;
}
*{margin:0;padding:0;box-sizing:border-box}
html,body{width:998px;height:1200px;overflow:hidden}
body{position:relative;background:var(--white);font-family:"Open Sans",Arial,sans-serif;color:var(--text)}
.abs{position:absolute}

/* Header */
.site-header{left:0;top:0;width:998px;height:78px;background:var(--header-bg);border-top:3px solid var(--green-line)}
.brand{left:110px;top:10px;display:flex;align-items:center;gap:8px}
.brand-mark{width:14px;height:14px;border-radius:50%;background:var(--green-dark)}
.brand-name{font-family:"Lato",sans-serif;font-weight:700;font-size:17px;line-height:17px;color:var(--green-dark);text-transform:uppercase;letter-spacing:.5px}
.phone-tab{left:694px;top:0;width:194px;height:32px}
.phone-number{left:758px;top:6px;font-family:"Lato",sans-serif;font-weight:700;font-size:15px;color:var(--white)}
.social{left:736px;top:40px;display:flex;gap:9px}
.social span{width:21px;height:21px;border-radius:3px;display:block}
.social .s1{background:#3b5998}.social .s2{background:#2aa9e0}.social .s3{background:#0077b5}.social .s4{background:#d34836}

/* Navigation */
.main-nav{left:0;top:78px;width:998px;height:39px;background:var(--green-dark)}
.main-nav ul{list-style:none;display:flex;position:absolute;left:110px;top:0;height:39px}
.main-nav li{font-family:"Lato",sans-serif;font-weight:700;font-size:11.5px;color:var(--white);line-height:39px;padding:0 5.5px;text-transform:uppercase}
.main-nav li.current{background:#e9e9e9;color:var(--green-dark);padding:0 5px}

/* Hero */
.hero{left:0;top:117px;width:998px;height:333px;background:linear-gradient(90deg,#c9b8a8 0%,#e1dcd3 25%,#6d5a6a 48%,#a8455a 62%,#2d5a55 78%,#c7cbd2 100%)}
.hero-caption{left:110px;top:207px;width:295px;height:183px;background:rgba(110,110,110,.62);border-radius:3px;padding:10px 11px;font-family:"Bree Serif",Georgia,serif;font-size:23.5px;line-height:33px;color:var(--white)}
.hero-dots{left:124px;top:411px;display:flex;gap:8px}
.hero-dots span{width:18px;height:18px;border-radius:50%;background:#8f8f8f}
.hero-dots span.active{background:#333}

/* Campus */
.section-title{left:0;top:466px;width:998px;text-align:center;font-size:28px;font-weight:300;color:#222}
.campus-card{top:520px;width:242px;height:78px;background:var(--navy);border-radius:2px}
.campus-card .icon{position:absolute;left:16px;top:12px;width:55px;height:55px;border-radius:50%;background:var(--white)}
.campus-card .icon svg{position:absolute;left:12px;top:12px}
.campus-card .label{position:absolute;left:86px;top:24px;font-family:"Oswald",sans-serif;font-size:21px;line-height:28px;color:var(--white)}

/* Welcome */
.welcome{left:0;top:626px;width:998px;height:238px;background:var(--teal)}
.welcome-kicker{left:111px;top:640px;font-family:"Oswald",sans-serif;font-size:21px;color:var(--white)}
.welcome-title{left:111px;top:660px;font-family:"Oswald",sans-serif;font-size:34px;color:var(--white)}
.welcome-rule{left:109px;top:714px;width:492px;border-top:2px dotted rgba(255,255,255,.6)}
.welcome-text{left:109px;top:726px;width:488px;font-size:12.3px;line-height:22.3px;color:var(--white)}
.read-more{left:525px;top:816px;font-size:12.3px;color:var(--white);text-decoration:underline}
.video-card{left:631px;top:638px;width:255px;height:203px;background:#f4f4f4;border-radius:3px;box-shadow:0 0 14px rgba(0,0,0,.25)}
.video-frame{left:641px;top:650px;width:235px;height:156px;background:linear-gradient(135deg,#dfe4ea 0%,#a9b6c4 45%,#8595a8 70%,#cfd6de 100%)}
.video-controls{left:641px;top:806px;width:235px;height:24px;background:#1e1e1e}

/* News */
.block-title{font-family:"Oswald",sans-serif;font-size:23px;color:var(--navy)}
.dashed{border-top:1px dashed var(--rule)}
.event{width:215px;height:50px}
.event .date{position:absolute;left:0;top:0;width:42px;height:47px;border:1px solid #bbb;background:#e6e6e6;border-bottom:2px solid var(--navy)}
.event .day{position:absolute;left:0;top:0;width:40px;height:25px;background:var(--navy);color:var(--white);font-size:15px;font-weight:700;text-align:center;line-height:25px}
.event .month{position:absolute;left:0;top:25px;width:40px;font-size:11px;text-align:center;line-height:20px;color:#333}
.event h4{position:absolute;left:53px;top:-2px;font-size:12px;font-weight:700;color:#222;white-space:nowrap}
.event p{position:absolute;left:53px;top:14px;width:170px;font-size:11px;line-height:16px;color:var(--muted)}
.column-divider{left:614px;top:925px;width:1px;height:140px;background:#dcdcdc}

/* Admissions */
.admissions-box{left:636px;top:932px;width:243px;height:149px;background:var(--navy);border-radius:2px;padding:6px 0 0 8px}
.admissions-box ul{list-style:none}
.admissions-box li{font-family:"Lato",sans-serif;font-size:12.5px;line-height:18.7px;color:var(--white);display:flex;align-items:center;gap:7px}

/* Footer */
.site-footer{left:0;top:1097px;width:998px;height:103px;background:linear-gradient(180deg,#3a3a3a 0%,#1f1f1f 100%)}
.footer-nav{left:0;top:1132px;width:998px;text-align:center;font-family:"Lato",sans-serif;font-size:11.5px;color:var(--white)}
.footer-nav span.sep{margin:0 5px}
.copyright{left:0;top:1159px;width:998px;text-align:center;font-family:"Lato",sans-serif;font-size:10.5px;color:var(--white)}
</style>
</head>
<body>

<header class="site-header abs"></header>
<div class="brand abs">
  <span class="brand-mark"></span>
  <div class="brand-name">Cedarvale<br>Ridge<br>College</div>
</div>
<svg class="phone-tab abs" viewBox="0 0 194 32" aria-hidden="true">
  <polygon points="0,0 194,0 182,32 12,32" fill="#003f35"/>
  <circle cx="47" cy="16" r="9" fill="#fff"/>
  <path d="M43.5 11.5c.8-.5 1.5 0 2 .9l.7 1.3c.3.6 0 1.1-.5 1.5l-.5.3c.5 1.3 1.5 2.5 2.8 3.1l.4-.5c.4-.5 1-.7 1.5-.3l1.2.8c.8.6 1 1.3.4 2-.9 1-2.3 1.2-3.6.5-2.2-1.1-3.9-2.9-4.9-5.1-.6-1.3-.5-3.3.5-4.5z" fill="#003f35"/>
</svg>
<div class="phone-number abs">604 555 0182</div>
<div class="social abs" aria-label="Social links">
  <span class="s1"></span><span class="s2"></span><span class="s3"></span><span class="s4"></span>
</div>

<nav class="main-nav abs">
  <ul>
    <li class="current">Home</li>
    <li>About Us</li>
    <li>Contact Us</li>
    <li>Consider Cedarvale</li>
    <li>Current Students</li>
    <li>Alumni</li>
    <li>Suporters</li>
    <li>News and Events</li>
    <li>Cedarvale Park</li>
  </ul>
</nav>

<section class="hero abs" role="img" aria-label="Photo of students talking on campus while holding books"></section>
<div class="hero-caption abs">Educating, equipping and enriching Christians for Spirit-empowered ministry in the chruch and in the world</div>
<div class="hero-dots abs"><span></span><span></span><span></span><span class="active"></span></div>

<h2 class="section-title abs">OUR CAMPUS</h2>
<div class="campus-card abs" style="left:109px">
  <div class="icon"><svg width="31" height="31" viewBox="0 0 31 31" aria-hidden="true"><path d="M15.5 2c-5 0-9 4-9 9 0 7 9 18 9 18s9-11 9-18c0-5-4-9-9-9z" fill="#4a9b5a"/><circle cx="15.5" cy="11" r="3.5" fill="#fff"/></svg></div>
  <div class="label">Map &amp; Directions</div>
</div>
<div class="campus-card abs" style="left:378px">
  <div class="icon"><svg width="31" height="31" viewBox="0 0 31 31" aria-hidden="true"><path d="M2 7l9-3 9 3 9-3v20l-9 3-9-3-9 3z" fill="#d8c59a" stroke="#9a8558"/><path d="M11 4v20M20 7v20" stroke="#9a8558"/></svg></div>
  <div class="label">Campus Map</div>
</div>
<div class="campus-card abs" style="left:647px">
  <div class="icon"><svg width="31" height="31" viewBox="0 0 31 31" aria-hidden="true"><rect x="3" y="6" width="25" height="19" fill="#fff" stroke="#888"/><rect x="6" y="9" width="19" height="13" fill="#8ec3e6"/><path d="M6 22l6-6 4 4 3-3 6 5z" fill="#5a8f5a"/></svg></div>
  <div class="label">Photo Gallery</div>
</div>

<section class="welcome abs"></section>
<div class="welcome-kicker abs">Welcome to</div>
<h1 class="welcome-title abs" style="font-weight:400">Cedarvale Ridge College</h1>
<div class="welcome-rule abs"></div>
<p class="welcome-text abs">Lorem ipsum dolor sit amet, consectetuer adipisemy nibh euismod tincidunt utre magmi aliquam erat volutpat. Ut wisi enim ad minim veniam quis nostrutation ullaeipit lobortisi nisl ut aliquip ex ea commodo consequis autem vel eum idolor in hendrer vulate velitm eonsequatvel illum dolore eu feugiat nulla facilisis at vero eros et accusao odiol digisml qui blandit praesent luptatum zzril delenit augue</p>
<a class="read-more abs">READ MORE</a>

<div class="video-card abs"></div>
<div class="video-frame abs" role="img" aria-label="Video still of a smiling staff member on campus"></div>
<svg class="abs" style="left:739px;top:708px" width="40" height="40" viewBox="0 0 40 40" aria-hidden="true"><circle cx="20" cy="20" r="20" fill="#fff"/><polygon points="16,12 29,20 16,28" fill="#111"/></svg>
<div class="video-controls abs"></div>
<svg class="abs" style="left:641px;top:806px" width="235" height="24" viewBox="0 0 235 24" aria-hidden="true">
  <rect width="24" height="24" fill="#3a3a3a"/>
  <polygon points="9,7 17,12 9,17" fill="#fff"/>
  <text x="35" y="16" fill="#fff" font-family="Lato,sans-serif" font-size="10" font-weight="700">04:59</text>
  <rect x="71" y="8" width="101" height="8" rx="4" fill="#555"/>
  <circle cx="116" cy="12" r="5" fill="#999"/>
  <text x="180" y="16" fill="#fff" font-family="Lato,sans-serif" font-size="10" font-weight="700">10:35</text>
  <polygon points="215,10 218,10 222,6 222,18 218,14 215,14" fill="#fff"/>
  <path d="M224.5 9a4 4 0 0 1 0 6" stroke="#fff" fill="none"/>
</svg>

<h3 class="block-title abs" style="left:107px;top:880px;font-weight:400">News &amp; Events</h3>
<svg class="abs" style="left:536px;top:889px" width="32" height="16" viewBox="0 0 32 16" aria-hidden="true"><path d="M8 2L3 8l5 6M24 2l5 6-5 6" stroke="#0d2356" stroke-width="2" fill="none"/></svg>
<div class="dashed abs" style="left:107px;top:921px;width:460px"></div>

<article class="event abs" style="left:109px;top:931px"><div class="date"><div class="day">18</div><div class="month">NOV</div></div><h4>Lorem ipsum dolor sit..</h4><p>Sed diam nonmy nibh eumod tincidun ut laoreet dolore magna</p></article>
<article class="event abs" style="left:355px;top:931px"><div class="date"><div class="day">20</div><div class="month">NOV</div></div><h4>Lorem ipsum dolor sit..</h4><p>Sed diam nonmy nibh eumod tincidun ut laoreet dolore magna</p></article>
<article class="event abs" style="left:109px;top:1002px"><div class="date"><div class="day">19</div><div class="month">NOV</div></div><h4>Lorem ipsum dolor sit..</h4><p>Sed diam nonmy nibh eumod tincidun ut laoreet dolore magna</p></article>
<article class="event abs" style="left:355px;top:1002px"><div class="date"><div class="day">21</div><div class="month">NOV</div></div><h4>Lorem ipsum dolor sit..</h4><p>Sed diam nonmy nibh eumod tincidun ut laoreet dolore magna</p></article>

<div class="column-divider abs"></div>

<h3 class="block-title abs" style="left:636px;top:880px;font-weight:400">Admissions</h3>
<div class="dashed abs" style="left:636px;top:921px;width:253px"></div>
<div class="admissions-box abs">
  <ul>
    <li><svg width="7" height="10" viewBox="0 0 7 10" aria-hidden="true"><path d="M1 1l4 4-4 4" stroke="#fff" stroke-width="1.6" fill="none"/></svg>Download the full Catalogue</li>
    <li><svg width="7" height="10" viewBox="0 0 7 10" aria-hidden="true"><path d="M1 1l4 4-4 4" stroke="#fff" stroke-width="1.6" fill="none"/></svg>Apply Today (Application Package)</li>
    <li><svg width="7" height="10" viewBox="0 0 7 10" aria-hidden="true"><path d="M1 1l4 4-4 4" stroke="#fff" stroke-width="1.6" fill="none"/></svg>Information Request</li>
    <li><svg width="7" height="10" viewBox="0 0 7 10" aria-hidden="true"><path d="M1 1l4 4-4 4" stroke="#fff" stroke-width="1.6" fill="none"/></svg>Browse our Programs</li>
    <li><svg width="7" height="10" viewBox="0 0 7 10" aria-hidden="true"><path d="M1 1l4 4-4 4" stroke="#fff" stroke-width="1.6" fill="none"/></svg>Download Forms</li>
    <li><svg width="7" height="10" viewBox="0 0 7 10" aria-hidden="true"><path d="M1 1l4 4-4 4" stroke="#fff" stroke-width="1.6" fill="none"/></svg>Admissions Information</li>
    <li><svg width="7" height="10" viewBox="0 0 7 10" aria-hidden="true"><path d="M1 1l4 4-4 4" stroke="#fff" stroke-width="1.6" fill="none"/></svg>Campus Directory</li>
  </ul>
</div>

<footer class="site-footer abs"></footer>
<div class="footer-nav abs">Home<span class="sep">|</span>About Us<span class="sep">|</span>Contact Us<span class="sep">|</span>Consider Cedarvale<span class="sep">|</span>Current Students<span class="sep">|</span>Alumni<span class="sep">|</span>Suporters<span class="sep">|</span>News And Events<span class="sep">|</span>Cedarvale Park</div>
<div class="copyright abs">© 2014 | Northgate Web Copyright | All Rights Reserved. | Privacy Policy</div>

</body>
</html>
```